Walk Beside The River

Business Card design

Target Market(s)

People who require support in the commnity

Industry/Entity Type

Mental Health Support

Contact Information for Business Card

Mental Health Support Rosalind Tavener walkbesidetheriver@mailcove.com.au 0481 637 092 PO Box 926 Coralwood QLD 4573

Colors
6B429C
8869AF
B7A5CE
E3DAEB
F3F0F8

Requirements
Must have
• Logo & details listed above
Should not have
• No red or orange

```html
<!DOCTYPE html>
<html lang="en">
<head>
<meta charset="utf-8">
<title>Walk Beside The River — Business Card</title>
<link rel="stylesheet" href="https://fonts.googleapis.com/css2?family=Inter:wght@400;700&display=swap">
<style>
  :root {
    --purple: #6b429c;
    --purple-mid: #8869af;
    --purple-soft: #b7a5ce;
    --lilac: #e3daeb;
    --paper: #f2f1ef;
    --ink: #6f6f72;
    --backdrop: #dcdde0;
  }
  * { margin: 0; padding: 0; box-sizing: border-box; }
  html, body { width: 1200px; height: 1051px; overflow: hidden; }
  body {
    background: var(--backdrop);
    font-family: "Inter", sans-serif;
    display: flex;
    flex-direction: column;
    align-items: center;
    justify-content: center;
    gap: 56px;
  }
  .card {
    width: 580px;
    height: 354px;
    background: var(--paper);
    border-bottom: 5px solid var(--purple);
    box-shadow: 0 18px 40px rgba(0,0,0,0.12);
    position: relative;
    display: flex;
    align-items: center;
  }
  .brand {
    display: flex;
    align-items: center;
    gap: 12px;
  }
  .brand-dot {
    width: 26px;
    height: 26px;
    border-radius: 50%;
    background: var(--purple);
    flex: none;
  }
  .brand-name {
    font-weight: 700;
    font-size: 20px;
    line-height: 1.2;
    color: var(--purple);
  }
  .card-front { padding-left: 40px; }
  .card-front .brand { width: 180px; }
  .divider {
    width: 2px;
    height: 190px;
    background: var(--purple);
    margin: 0 24px 0 20px;
  }
  .details { color: var(--ink); font-size: 14px; line-height: 1.45; }
  .details .role, .details .person {
    color: var(--purple);
    font-weight: 700;
    font-size: 17px;
    line-height: 1.25;
  }
  .details .address { margin-top: 12px; }
  .contact { display: flex; align-items: center; gap: 7px; }
  .details .contact-phone { margin-top: 4px; }
  .contact svg { width: 12px; height: 12px; flex: none; fill: var(--purple); }
  .card-back { justify-content: center; }
  .card-back .brand-name { font-size: 26px; }
  .card-back .brand-dot { width: 34px; height: 34px; }
</style>
</head>
<body>
  <section class="card card-front">
    <div class="brand">
      <span class="brand-dot"></span>
      <span class="brand-name">Walk Beside<br>The River</span>
    </div>
    <div class="divider"></div>
    <div class="details">
      <p class="role">Mental Health Support</p>
      <p class="person">Rosalind Tavener</p>
      <p class="address">PO Box 926<br>Coralwood QLD 4573</p>
      <p class="contact contact-phone">
        <svg viewBox="0 0 24 24" aria-hidden="true"><path d="M6.6 10.8a15.1 15.1 0 0 0 6.6 6.6l2.2-2.2a1 1 0 0 1 1-.25 11.4 11.4 0 0 0 3.6.57 1 1 0 0 1 1 1V20a1 1 0 0 1-1 1A17 17 0 0 1 3 4a1 1 0 0 1 1-1h3.5a1 1 0 0 1 1 1c0 1.25.2 2.45.57 3.57a1 1 0 0 1-.25 1z"/></svg>
        <span>0481 637 092</span>
      </p>
      <p class="contact contact-email">
        <svg viewBox="0 0 24 24" aria-hidden="true"><path d="M2 5h20v14H2z M2 5l10 8 10-8" /></svg>
        <span>walkbesidetheriver@mailcove.com.au</span>
      </p>
    </div>
  </section>
  <section class="card card-back">
    <div class="brand">
      <span class="brand-dot"></span>
      <span class="brand-name">Walk Beside The River</span>
    </div>
  </section>
</body>
</html>
```